Sleek, luxurious B&W packaging for sensual new massager product

We require packaging for our new product, a sleek new massager wand. The packaging needs to be black and white, and needs to represent our brand. The words to describe our brand are:

Sensual
Luxurious
Sleek simplicity

Here is a Pinboardly board detailing our preferred style: https://uk.pinboardly.example/moravtenley/packaging-velorine/

We love the stand out simplicity of Duvree packaging, for example.

Further details and requirements are attached.

Target Market(s)

Female, 18-55yo.

Industry/Entity Type

Fashion

Font styles to use
Sans Serif

Colors
000000
ffffff

Requirements
Must have
• See attached for explanation of requirements.
• DETAILED REQUIREMENTS
• BOX FRONT:
• LOGO
• CORDLESS MINI WAND MASSAGER
• www.quelvoro.example
• BOX SIDE 1:
• ICON
• Sleek, Cordless design
• ICON
• 100% Waterproof
• ICON
• USB Rechargable
• ICON
• 8x Stimulating Speeds
• ICON
• 20x Heavenly Pulsations
• ICON
• Discreetly Quiet
• ICON
• Body-safe Silicone
• ICON
• Phthalate-free
• BOX SIDE 2
• The Velorine was created for your theraputic satisfaction.
• Delight your body with 8 Stimulating Speeds & 20 Heavenly Pulsations of Massage Pleasure.
• Where will Velorine take you?
• LOGO
• www.quelvoro.example
• BOX BASE:
• Colour: Aubergine
• Size: 7.8” (L) x 1.6” (W) / 200MM (L) x 41MM (W)
• Weight: 6.5 ounces / 186G
• Material: Body-Safe Medical Grade Silicone + ABS
• Battery: Li-oh 1200MAH 3.7V
• Charging: 1.5 hours at 5V 500MA
• Sound Output: =<40DB
• User time: up to 3 hours
• Model: 00000000-000000000
• LOGO
• www.quelvoro.example
• 1 year warranty (ICON)
• CE logo + barcode (awaiting)
Nice to have
• Sleek, luxury, black and white design.
• Here's our pinboardly board of ideas: https://uk.pinboardly.example/moravtenley/packaging-velorine/
• I am open to both a landscape or portrait box design. Possibly portrait looks more elegant.
Should not have
• Too much text.
• Too much fussiness.

```html
<!DOCTYPE html>
<html lang="en">
<head>
<meta charset="utf-8">
<title>Velorine Packaging Range</title>
<link rel="stylesheet" href="https://fonts.googleapis.com/css2?family=Open+Sans:wght@300;400&display=swap">
<style>
  :root {
    --ink: #000000;
    --paper: #ffffff;
    --stage: #ffffff;
    --edge: #d6d6d6;
    --side: #f4f4f4;
    --font-text: "Open Sans", Arial, sans-serif;
  }
  * { box-sizing: border-box; margin: 0; padding: 0; }
  html, body { width: 1200px; height: 1156px; overflow: hidden; background: var(--stage); }
  .range { position: relative; width: 1200px; height: 1156px; }

  .box { position: absolute; width: 480px; height: 200px; font-family: var(--font-text); color: var(--ink); }
  .box--a { left: 90px;  top: 60px; }
  .box--b { left: 630px; top: 60px; }
  .box--c { left: 90px;  top: 330px; }
  .box--d { left: 630px; top: 330px; }
  .box--e { left: 90px;  top: 600px; }
  .box--f { left: 630px; top: 600px; }
  .box--g { left: 360px; top: 870px; }

  .front { position: absolute; left: 0; top: 0; width: 420px; height: 150px; background: var(--paper); border: 1px solid var(--edge); overflow: hidden; }
  .pattern { position: absolute; inset: 0; }
  .pattern--a { background: linear-gradient(90deg, var(--paper) 0%, #e9e9e9 100%); }
  .pattern--b { background: linear-gradient(180deg, #dcdcdc 0%, var(--paper) 100%); }
  .pattern--c { background: linear-gradient(135deg, var(--paper) 0%, #d0d0d0 100%); }
  .pattern--d { background: var(--ink); }
  .pattern--e { background: linear-gradient(90deg, var(--ink) 0%, #2e2e2e 100%); }
  .pattern--f { background: radial-gradient(circle at 50% 50%, #9a9a9a 0%, var(--ink) 100%); }
  .pattern--g { background: linear-gradient(45deg, #1c1c1c 0%, #6e6e6e 100%); }

  .label { position: absolute; left: 84px; top: 22px; width: 252px; height: 106px; background: var(--paper); border: 1px solid var(--ink); display: flex; flex-direction: column; align-items: center; justify-content: center; text-align: center; }
  .label__brand { font-size: 17px; font-weight: 300; letter-spacing: 1px; line-height: 1; }
  .label__maker { font-size: 5px; font-weight: 400; letter-spacing: 2px; margin-top: 4px; color: #555; }
  .label__product { font-size: 8px; font-weight: 400; letter-spacing: 0.4px; margin-top: 12px; }
  .label__url { font-size: 7px; font-weight: 400; letter-spacing: 1.5px; margin-top: 13px; }

  .base { position: absolute; left: 0; top: 150px; width: 420px; height: 50px; background: var(--side); border: 1px solid var(--edge); border-top: none; display: flex; justify-content: space-around; align-items: center; padding: 0 8px; }
  .feature { display: flex; flex-direction: column; align-items: center; width: 46px; }
  .feature__icon { width: 12px; height: 12px; }
  .feature__text { font-size: 5px; font-weight: 400; text-align: center; margin-top: 3px; line-height: 1.2; text-transform: uppercase; white-space: nowrap; }

  .end { position: absolute; left: 420px; top: 0; width: 60px; height: 200px; background: var(--paper); border: 1px solid var(--edge); border-left: none; display: flex; align-items: center; justify-content: center; gap: 8px; }
  .end__brand, .end__url { writing-mode: vertical-rl; font-weight: 300; }
  .end__brand { font-size: 10px; letter-spacing: 1px; }
  .end__url { font-size: 6px; letter-spacing: 1.5px; }
</style>
</head>
<body>
<main class="range">

  <section class="box box--a">
    <div class="front">
      <div class="pattern pattern--a" role="img" aria-label="Fine broken zigzag line pattern in black on white"></div>
      <div class="label"><span class="label__brand">Velorine</span><span class="label__maker">BY QUELVORO</span><span class="label__product">CORDLESS MINI WAND MASSAGER</span><span class="label__url">www.quelvoro.example</span></div>
    </div>
    <div class="base">
      <div class="feature"><svg class="feature__icon" viewBox="0 0 12 12"><circle cx="6" cy="6" r="5" fill="none" stroke="#000"/></svg><span class="feature__text">Cordless</span></div>
      <div class="feature"><svg class="feature__icon" viewBox="0 0 12 12"><path d="M6 1 L10 7 A4 4 0 0 1 2 7 Z" fill="#000"/></svg><span class="feature__text">Waterproof</span></div>
      <div class="feature"><svg class="feature__icon" viewBox="0 0 12 12"><rect x="4" y="1" width="4" height="10" rx="1" fill="none" stroke="#000"/></svg><span class="feature__text">USB Charge</span></div>
      <div class="feature"><svg class="feature__icon" viewBox="0 0 12 12"><path d="M1 9 Q6 1 11 9" fill="none" stroke="#000"/></svg><span class="feature__text">8x Speeds</span></div>
      <div class="feature"><svg class="feature__icon" viewBox="0 0 12 12"><path d="M1 6 Q3 2 6 6 T11 6" fill="none" stroke="#000"/></svg><span class="feature__text">20x Pulses</span></div>
      <div class="feature"><svg class="feature__icon" viewBox="0 0 12 12"><circle cx="6" cy="6" r="5" fill="#000"/></svg><span class="feature__text">Quiet</span></div>
      <div class="feature"><svg class="feature__icon" viewBox="0 0 12 12"><rect x="1" y="1" width="10" height="10" fill="#000"/></svg><span class="feature__text">Silicone</span></div>
      <div class="feature"><svg class="feature__icon" viewBox="0 0 12 12"><circle cx="6" cy="6" r="5" fill="none" stroke="#000" stroke-width="2"/></svg><span class="feature__text">No Phthalate</span></div>
    </div>
    <div class="end"><span class="end__brand">Velorine</span><span class="end__url">www.quelvoro.example</span></div>
  </section>

  <section class="box box--b">
    <div class="front">
      <div class="pattern pattern--b" role="img" aria-label="Rows of black zigzag lines on white"></div>
      <div class="label"><span class="label__brand">Velorine</span><span class="label__maker">BY QUELVORO</span><span class="label__product">CORDLESS MINI WAND MASSAGER</span><span class="label__url">www.quelvoro.example</span></div>
    </div>
    <div class="base">
      <div class="feature"><svg class="feature__icon" viewBox="0 0 12 12"><circle cx="6" cy="6" r="5" fill="none" stroke="#000"/></svg><span class="feature__text">Cordless</span></div>
      <div class="feature"><svg class="feature__icon" viewBox="0 0 12 12"><path d="M6 1 L10 7 A4 4 0 0 1 2 7 Z" fill="#000"/></svg><span class="feature__text">Waterproof</span></div>
      <div class="feature"><svg class="feature__icon" viewBox="0 0 12 12"><rect x="4" y="1" width="4" height="10" rx="1" fill="none" stroke="#000"/></svg><span class="feature__text">USB Charge</span></div>
      <div class="feature"><svg class="feature__icon" viewBox="0 0 12 12"><path d="M1 9 Q6 1 11 9" fill="none" stroke="#000"/></svg><span class="feature__text">8x Speeds</span></div>
      <div class="feature"><svg class="feature__icon" viewBox="0 0 12 12"><path d="M1 6 Q3 2 6 6 T11 6" fill="none" stroke="#000"/></svg><span class="feature__text">20x Pulses</span></div>
      <div class="feature"><svg class="feature__icon" viewBox="0 0 12 12"><circle cx="6" cy="6" r="5" fill="#000"/></svg><span class="feature__text">Quiet</span></div>
      <div class="feature"><svg class="feature__icon" viewBox="0 0 12 12"><rect x="1" y="1" width="10" height="10" fill="#000"/></svg><span class="feature__text">Silicone</span></div>
      <div class="feature"><svg class="feature__icon" viewBox="0 0 12 12"><circle cx="6" cy="6" r="5" fill="none" stroke="#000" stroke-width="2"/></svg><span class="feature__text">No Phthalate</span></div>
    </div>
    <div class="end"><span class="end__brand">Velorine</span><span class="end__url">www.quelvoro.example</span></div>
  </section>

  <section class="box box--c">
    <div class="front">
      <div class="pattern pattern--c" role="img" aria-label="Open black chevron lattice pattern on white"></div>
      <div class="label"><span class="label__brand">Velorine</span><span class="label__maker">BY QUELVORO</span><span class="label__product">CORDLESS MINI WAND MASSAGER</span><span class="label__url">www.quelvoro.example</span></div>
    </div>
    <div class="base">
      <div class="feature"><svg class="feature__icon" viewBox="0 0 12 12"><circle cx="6" cy="6" r="5" fill="none" stroke="#000"/></svg><span class="feature__text">Cordless</span></div>
      <div class="feature"><svg class="feature__icon" viewBox="0 0 12 12"><path d="M6 1 L10 7 A4 4 0 0 1 2 7 Z" fill="#000"/></svg><span class="feature__text">Waterproof</span></div>
      <div class="feature"><svg class="feature__icon" viewBox="0 0 12 12"><rect x="4" y="1" width="4" height="10" rx="1" fill="none" stroke="#000"/></svg><span class="feature__text">USB Charge</span></div>
      <div class="feature"><svg class="feature__icon" viewBox="0 0 12 12"><path d="M1 9 Q6 1 11 9" fill="none" stroke="#000"/></svg><span class="feature__text">8x Speeds</span></div>
      <div class="feature"><svg class="feature__icon" viewBox="0 0 12 12"><path d="M1 6 Q3 2 6 6 T11 6" fill="none" stroke="#000"/></svg><span class="feature__text">20x Pulses</span></div>
      <div class="feature"><svg class="feature__icon" viewBox="0 0 12 12"><circle cx="6" cy="6" r="5" fill="#000"/></svg><span class="feature__text">Quiet</span></div>
      <div class="feature"><svg class="feature__icon" viewBox="0 0 12 12"><rect x="1" y="1" width="10" height="10" fill="#000"/></svg><span class="feature__text">Silicone</span></div>
      <div class="feature"><svg class="feature__icon" viewBox="0 0 12 12"><circle cx="6" cy="6" r="5" fill="none" stroke="#000" stroke-width="2"/></svg><span class="feature__text">No Phthalate</span></div>
    </div>
    <div class="end"><span class="end__brand">Velorine</span><span class="end__url">www.quelvoro.example</span></div>
  </section>

  <section class="box box--d">
    <div class="front">
      <div class="pattern pattern--d" role="img" aria-label="Dense black wavy stripe pattern on white"></div>
      <div class="label"><span class="label__brand">Velorine</span><span class="label__maker">BY QUELVORO</span><span class="label__product">CORDLESS MINI WAND MASSAGER</span><span class="label__url">www.quelvoro.example</span></div>
    </div>
    <div class="base">
      <div class="feature"><svg class="feature__icon" viewBox="0 0 12 12"><circle cx="6" cy="6" r="5" fill="none" stroke="#000"/></svg><span class="feature__text">Cordless</span></div>
      <div class="feature"><svg class="feature__icon" viewBox="0 0 12 12"><path d="M6 1 L10 7 A4 4 0 0 1 2 7 Z" fill="#000"/></svg><span class="feature__text">Waterproof</span></div>
      <div class="feature"><svg class="feature__icon" viewBox="0 0 12 12"><rect x="4" y="1" width="4" height="10" rx="1" fill="none" stroke="#000"/></svg><span class="feature__text">USB Charge</span></div>
      <div class="feature"><svg class="feature__icon" viewBox="0 0 12 12"><path d="M1 9 Q6 1 11 9" fill="none" stroke="#000"/></svg><span class="feature__text">8x Speeds</span></div>
      <div class="feature"><svg class="feature__icon" viewBox="0 0 12 12"><path d="M1 6 Q3 2 6 6 T11 6" fill="none" stroke="#000"/></svg><span class="feature__text">20x Pulses</span></div>
      <div class="feature"><svg class="feature__icon" viewBox="0 0 12 12"><circle cx="6" cy="6" r="5" fill="#000"/></svg><span class="feature__text">Quiet</span></div>
      <div class="feature"><svg class="feature__icon" viewBox="0 0 12 12"><rect x="1" y="1" width="10" height="10" fill="#000"/></svg><span class="feature__text">Silicone</span></div>
      <div class="feature"><svg class="feature__icon" viewBox="0 0 12 12"><circle cx="6" cy="6" r="5" fill="none" stroke="#000" stroke-width="2"/></svg><span class="feature__text">No Phthalate</span></div>
    </div>
    <div class="end"><span class="end__brand">Velorine</span><span class="end__url">www.quelvoro.example</span></div>
  </section>

  <section class="box box--e">
    <div class="front">
      <div class="pattern pattern--e" role="img" aria-label="Bold black herringbone chevron pattern on white"></div>
      <div class="label"><span class="label__brand">Velorine</span><span class="label__maker">BY QUELVORO</span><span class="label__product">CORDLESS MINI WAND MASSAGER</span><span class="label__url">www.quelvoro.example</span></div>
    </div>
    <div class="base">
      <div class="feature"><svg class="feature__icon" viewBox="0 0 12 12"><circle cx="6" cy="6" r="5" fill="none" stroke="#000"/></svg><span class="feature__text">Cordless</span></div>
      <div class="feature"><svg class="feature__icon" viewBox="0 0 12 12"><path d="M6 1 L10 7 A4 4 0 0 1 2 7 Z" fill="#000"/></svg><span class="feature__text">Waterproof</span></div>
      <div class="feature"><svg class="feature__icon" viewBox="0 0 12 12"><rect x="4" y="1" width="4" height="10" rx="1" fill="none" stroke="#000"/></svg><span class="feature__text">USB Charge</span></div>
      <div class="feature"><svg class="feature__icon" viewBox="0 0 12 12"><path d="M1 9 Q6 1 11 9" fill="none" stroke="#000"/></svg><span class="feature__text">8x Speeds</span></div>
      <div class="feature"><svg class="feature__icon" viewBox="0 0 12 12"><path d="M1 6 Q3 2 6 6 T11 6" fill="none" stroke="#000"/></svg><span class="feature__text">20x Pulses</span></div>
      <div class="feature"><svg class="feature__icon" viewBox="0 0 12 12"><circle cx="6" cy="6" r="5" fill="#000"/></svg><span class="feature__text">Quiet</span></div>
      <div class="feature"><svg class="feature__icon" viewBox="0 0 12 12"><rect x="1" y="1" width="10" height="10" fill="#000"/></svg><span class="feature__text">Silicone</span></div>
      <div class="feature"><svg class="feature__icon" viewBox="0 0 12 12"><circle cx="6" cy="6" r="5" fill="none" stroke="#000" stroke-width="2"/></svg><span class="feature__text">No Phthalate</span></div>
    </div>
    <div class="end"><span class="end__brand">Velorine</span><span class="end__url">www.quelvoro.example</span></div>
  </section>

  <section class="box box--f">
    <div class="front">
      <div class="pattern pattern--f" role="img" aria-label="Flowing black wave stripe pattern on white"></div>
      <div class="label"><span class="label__brand">Velorine</span><span class="label__maker">BY QUELVORO</span><span class="label__product">CORDLESS MINI WAND MASSAGER</span><span class="label__url">www.quelvoro.example</span></div>
    </div>
    <div class="base">
      <div class="feature"><svg class="feature__icon" viewBox="0 0 12 12"><circle cx="6" cy="6" r="5" fill="none" stroke="#000"/></svg><span class="feature__text">Cordless</span></div>
      <div class="feature"><svg class="feature__icon" viewBox="0 0 12 12"><path d="M6 1 L10 7 A4 4 0 0 1 2 7 Z" fill="#000"/></svg><span class="feature__text">Waterproof</span></div>
      <div class="feature"><svg class="feature__icon" viewBox="0 0 12 12"><rect x="4" y="1" width="4" height="10" rx="1" fill="none" stroke="#000"/></svg><span class="feature__text">USB Charge</span></div>
      <div class="feature"><svg class="feature__icon" viewBox="0 0 12 12"><path d="M1 9 Q6 1 11 9" fill="none" stroke="#000"/></svg><span class="feature__text">8x Speeds</span></div>
      <div class="feature"><svg class="feature__icon" viewBox="0 0 12 12"><path d="M1 6 Q3 2 6 6 T11 6" fill="none" stroke="#000"/></svg><span class="feature__text">20x Pulses</span></div>
      <div class="feature"><svg class="feature__icon" viewBox="0 0 12 12"><circle cx="6" cy="6" r="5" fill="#000"/></svg><span class="feature__text">Quiet</span></div>
      <div class="feature"><svg class="feature__icon" viewBox="0 0 12 12"><rect x="1" y="1" width="10" height="10" fill="#000"/></svg><span class="feature__text">Silicone</span></div>
      <div class="feature"><svg class="feature__icon" viewBox="0 0 12 12"><circle cx="6" cy="6" r="5" fill="none" stroke="#000" stroke-width="2"/></svg><span class="feature__text">No Phthalate</span></div>
    </div>
    <div class="end"><span class="end__brand">Velorine</span><span class="end__url">www.quelvoro.example</span></div>
  </section>

  <section class="box box--g">
    <div class="front">
      <div class="pattern pattern--g" role="img" aria-label="Fine concentric diamond pattern in black and white"></div>
      <div class="label"><span class="label__brand">Velorine</span><span class="label__maker">BY QUELVORO</span><span class="label__product">CORDLESS MINI WAND MASSAGER</span><span class="label__url">www.quelvoro.example</span></div>
    </div>
    <div class="base">
      <div class="feature"><svg class="feature__icon" viewBox="0 0 12 12"><circle cx="6" cy="6" r="5" fill="none" stroke="#000"/></svg><span class="feature__text">Cordless</span></div>
      <div class="feature"><svg class="feature__icon" viewBox="0 0 12 12"><path d="M6 1 L10 7 A4 4 0 0 1 2 7 Z" fill="#000"/></svg><span class="feature__text">Waterproof</span></div>
      <div class="feature"><svg class="feature__icon" viewBox="0 0 12 12"><rect x="4" y="1" width="4" height="10" rx="1" fill="none" stroke="#000"/></svg><span class="feature__text">USB Charge</span></div>
      <div class="feature"><svg class="feature__icon" viewBox="0 0 12 12"><path d="M1 9 Q6 1 11 9" fill="none" stroke="#000"/></svg><span class="feature__text">8x Speeds</span></div>
      <div class="feature"><svg class="feature__icon" viewBox="0 0 12 12"><path d="M1 6 Q3 2 6 6 T11 6" fill="none" stroke="#000"/></svg><span class="feature__text">20x Pulses</span></div>
      <div class="feature"><svg class="feature__icon" viewBox="0 0 12 12"><circle cx="6" cy="6" r="5" fill="#000"/></svg><span class="feature__text">Quiet</span></div>
      <div class="feature"><svg class="feature__icon" viewBox="0 0 12 12"><rect x="1" y="1" width="10" height="10" fill="#000"/></svg><span class="feature__text">Silicone</span></div>
      <div class="feature"><svg class="feature__icon" viewBox="0 0 12 12"><circle cx="6" cy="6" r="5" fill="none" stroke="#000" stroke-width="2"/></svg><span class="feature__text">No Phthalate</span></div>
    </div>
    <div class="end"><span class="end__brand">Velorine</span><span class="end__url">www.quelvoro.example</span></div>
  </section>

</main>
</body>
</html>
```